Dean Hartwell realestate

We want something complete different to our website now and something that will stand out this is our website http://deanhartwellrealestate.com/

our company website for my boss is www.gordonvale.com

please note this website is being made for dean hartwell not gordon vale

something similar to our company website but has to be in the branding of dean hartwell realestate

```html
<!DOCTYPE html>
<html lang="en">
<head>
<meta charset="utf-8">
<title>Dean Hartwell Real Estate</title>
<link href="https://fonts.googleapis.com/css2?family=Lato:ital,wght@0,400;0,700;0,900;1,400&display=swap" rel="stylesheet">
<style>
:root{
  --orange:#f57c0f;
  --ink:#2b2b2b;
  --text:#444;
  --muted:#666;
  --line:#e2e2e2;
  --white:#fff;
  --dark:#1c1c1c;
  --darker:#121212;
  --hero-a:#2a2f45;
  --hero-b:#7a5b4a;
  --hero-c:#3b4a2a;
}
*{box-sizing:border-box;margin:0;padding:0}
html,body{width:1200px;height:2990px;overflow:hidden;background:var(--white)}
body{position:relative;font-family:'Lato',sans-serif;color:var(--text)}
.abs{position:absolute}

/* header */
.site-header{position:absolute;left:0;top:0;width:1200px;height:78px;background:var(--white);z-index:5}
.nav-link{position:absolute;top:31px;font-size:14px;font-weight:700;color:var(--ink);text-transform:uppercase;letter-spacing:.3px}
.nav-link.active{color:var(--orange)}
.brand{position:absolute;left:476px;top:0;width:248px;height:138px;z-index:6}
.brand-name{position:absolute;left:0;top:22px;width:248px;text-align:center;font-size:26px;font-weight:700;line-height:36px;color:var(--ink);white-space:nowrap;letter-spacing:.2px}
.social{position:absolute;top:32px;width:16px;height:16px;border-radius:50%;background:#333}

/* hero */
.hero{position:absolute;left:0;top:78px;width:1200px;height:622px;clip-path:polygon(0 0,100% 0,100% 89%,0 100%)}
.hero-photo{position:absolute;inset:0;background:linear-gradient(180deg,var(--hero-a) 0%,#4d4550 35%,var(--hero-b) 62%,var(--hero-c) 100%)}
.hero-title{position:absolute;left:74px;top:218px;font-size:42px;font-weight:900;line-height:46px;color:var(--white);text-transform:uppercase}
.btn{display:block;background:var(--orange);color:var(--white);font-weight:700;text-transform:uppercase;text-align:center}
.hero-btn{position:absolute;left:74px;top:334px;width:180px;height:40px;line-height:40px;font-size:14px}
.hero-phone{position:absolute;left:74px;top:404px;font-size:30px;font-weight:900;color:var(--white);display:flex;align-items:center;gap:14px}
.hero-video{position:absolute;left:796px;top:342px;width:332px;height:170px;border:4px solid var(--white);background:linear-gradient(135deg,#5f6f5a,#3b4a36 60%,#2c3a2a)}
.play{position:absolute;left:146px;top:62px;width:36px;height:36px;border-radius:50%;background:rgba(255,255,255,.85)}

/* quick links */
.quick{position:absolute;top:610px;width:200px;text-align:center}
.quick-icon{width:120px;height:120px;margin:0 auto;border-radius:50%;background:var(--white);border:5px solid #e6e6e6;display:flex;align-items:center;justify-content:center}
.quick-label{margin-top:20px;font-size:18px;font-weight:700;color:var(--orange);text-transform:uppercase}
.divider{position:absolute;left:80px;top:846px;width:1050px;height:1px;background:var(--line)}

.section-title{position:absolute;left:0;width:1200px;text-align:center;font-size:34px;font-weight:700;color:var(--ink);text-transform:uppercase}

/* property cards */
.card{position:absolute;width:512px;height:204px;border:1px solid var(--line);background:var(--white)}
.card-photo{position:absolute;left:15px;top:18px;width:234px;height:168px;background:linear-gradient(180deg,#5d7fb3 0%,#a8a9b2 45%,#8a5a44 75%,#4f4a3c 100%)}
.sold{position:absolute;background:#1e1e1e;color:var(--white);font-size:13px;font-weight:700;padding:7px 13px}
.card-title{position:absolute;left:268px;top:44px;font-size:15px;font-weight:700;line-height:24px;color:var(--orange);text-transform:uppercase;white-space:nowrap}
.card-text{position:absolute;left:268px;top:96px;width:212px;font-size:13px;line-height:23px;color:var(--text)}

/* appraisal */
.appraisal{position:absolute;left:0;top:1638px;width:1200px;height:460px;clip-path:polygon(0 0,100% 10%,100% 100%,0 92%)}
.appraisal-photo{position:absolute;inset:0;background:linear-gradient(90deg,#1d2233 0%,#3a3a44 40%,#6d5a48 70%,#2b2f35 100%)}
.appraisal .section-title{color:var(--white);top:92px}
.field{position:absolute;background:var(--white);font-size:13px;color:#333;padding:0 14px;display:flex;align-items:center;height:40px;width:334px;left:254px}
.field.area{align-items:flex-start;padding-top:12px;left:612px;top:152px;height:186px;width:334px}
.appraisal-submit{position:absolute;left:612px;top:350px;width:334px;height:40px;line-height:40px;font-size:16px}

/* testimonials */
.quote{position:absolute;top:2206px;width:356px}
.quote-mark{position:absolute;left:0;top:0;width:38px;height:38px;border-radius:50%;background:var(--orange);color:var(--white);font-size:34px;font-weight:900;text-align:center;line-height:46px}
.quote-body{position:absolute;left:60px;top:0;width:270px;font-size:13px;font-style:italic;line-height:26px;color:var(--text)}
.quote-name{position:absolute;left:60px;top:212px;font-size:13px;font-weight:700;color:var(--orange);text-transform:uppercase}
.quote-place{position:absolute;left:60px;top:236px;font-size:13px;font-style:italic;color:var(--text)}

/* footer */
.contact{position:absolute;left:0;top:2482px;width:1200px;height:432px;background:var(--dark);clip-path:polygon(0 17%,100% 0,100% 100%,0 100%)}
.contact .section-title{color:var(--white);top:108px}
.addr-head{position:absolute;left:76px;top:178px;font-size:14px;font-weight:700;color:var(--white)}
.addr{position:absolute;left:76px;top:204px;font-size:13px;line-height:21px;color:#bbb}
.addr .org{color:var(--orange);font-weight:700}
.map{position:absolute;left:342px;top:174px;width:242px;height:198px;background:linear-gradient(135deg,#e9e6df,#d7dbd2 60%,#cfd8e0)}
.form-head{position:absolute;left:614px;top:178px;font-size:14px;font-weight:700;color:var(--white);text-transform:uppercase}
.cfield{position:absolute;background:var(--white);font-size:13px;color:#333;padding:0 10px;height:34px;display:flex;align-items:center;top:210px}
.cfield.area{left:614px;top:258px;width:514px;height:72px;align-items:flex-start;padding-top:10px}
.contact-submit{position:absolute;left:614px;top:344px;width:514px;height:38px;line-height:38px;font-size:16px}
.copyright{position:absolute;left:0;top:2914px;width:1200px;height:76px;background:var(--darker);text-align:center;line-height:76px;font-size:12px;color:#999}
</style>
</head>
<body>

<header class="site-header">
  <a class="nav-link active" style="left:136px">Home</a>
  <a class="nav-link" style="left:224px">For Sale</a>
  <a class="nav-link" style="left:334px">Agents</a>
  <a class="nav-link" style="left:768px">Book Appraisal</a>
  <a class="nav-link" style="left:932px">Contact</a>
  <span class="social" style="left:1040px"></span>
  <span class="social" style="left:1074px"></span>
  <span class="social" style="left:1110px"></span>
</header>

<div class="brand">
  <svg class="abs" style="left:0;top:0" width="248" height="138" viewBox="0 0 248 138">
    <path d="M0 0H248V128L232 120H16L0 128Z" fill="#fff"/>
  </svg>
  <div class="brand-name">DEAN HARTWELL<br>PROPERTY</div>
</div>

<section class="hero">
  <div class="hero-photo" role="img" aria-label="Photo of a brick house with a pergola and lawn at dusk"></div>
  <h1 class="hero-title">Welcome to<br>Dean Hartwell Real Estate</h1>
  <a class="btn hero-btn">View Properties</a>
  <div class="hero-phone">
    <svg width="24" height="24" viewBox="0 0 24 24"><path d="M6.6 10.8a15.1 15.1 0 0 0 6.6 6.6l2.2-2.2c.3-.3.7-.4 1-.2 1.1.4 2.3.6 3.6.6.6 0 1 .4 1 1V20c0 .6-.4 1-1 1A17 17 0 0 1 3 4c0-.6.4-1 1-1h3.5c.6 0 1 .4 1 1 0 1.3.2 2.5.6 3.6.1.3 0 .7-.2 1z" fill="#fff"/></svg>
    CALL 0412 555 308
  </div>
  <div class="hero-video" role="img" aria-label="Video still of the agent standing in a park">
    <span class="play"></span>
    <svg class="abs" style="left:160px;top:72px" width="14" height="16" viewBox="0 0 14 16"><path d="M0 0L14 8L0 16Z" fill="#555"/></svg>
  </div>
</section>

<div class="quick" style="left:232px">
  <div class="quick-icon"><svg width="44" height="40" viewBox="0 0 44 40"><path d="M22 2L2 20h6v18h10V26h8v12h10V20h6z" fill="#333"/></svg></div>
  <div class="quick-label">For Sale</div>
</div>
<div class="quick" style="left:502px">
  <div class="quick-icon"><svg width="48" height="40" viewBox="0 0 48 40"><circle cx="14" cy="10" r="6" fill="#333"/><circle cx="34" cy="10" r="6" fill="#333"/><circle cx="24" cy="16" r="7" fill="#333"/><path d="M2 32c0-7 5-12 12-12 3 0 5 1 7 2-4 2-7 6-7 10z M46 32c0-7-5-12-12-12-3 0-5 1-7 2 4 2 7 6 7 10z M12 38c0-7 5-13 12-13s12 6 12 13z" fill="#333"/></svg></div>
  <div class="quick-label">Agents</div>
</div>
<div class="quick" style="left:772px">
  <div class="quick-icon"><svg width="34" height="42" viewBox="0 0 34 42"><path d="M2 2h20l10 10v28H2z" fill="#333"/><path d="M22 2v10h10" fill="#777"/><rect x="8" y="20" width="18" height="3" fill="#fff"/><rect x="8" y="26" width="18" height="3" fill="#fff"/><rect x="8" y="32" width="18" height="3" fill="#fff"/></svg></div>
  <div class="quick-label">Book Appraisal</div>
</div>

<div class="divider"></div>

<h2 class="section-title" style="top:880px">Latest Properties Sold</h2>

<article class="card" style="left:76px;top:952px">
  <div class="card-photo" role="img" aria-label="Photo of a single-storey house at dusk"></div><span class="sold" style="left:27px;top:28px">SOLD</span>
  <h3 class="card-title">12 Wren Street<br>Ashbury, 6191</h3>
  <p class="card-text">Lanventore veritatis et quasi architecto beatae vitae dicta sunt enim ipsam voluptatem ..</p>
</article>
<article class="card" style="left:612px;top:952px">
  <div class="card-photo" role="img" aria-label="Photo of a modern two-storey house with lit windows"></div><span class="sold" style="left:27px;top:28px">SOLD</span>
  <h3 class="card-title">7 Fennel Street<br>Brooklea,&nbsp; 6192</h3>
  <p class="card-text">Lanventore veritatis et quasi architecto beatae vitae dicta sunt enim ipsam voluptatem ..</p>
</article>
<article class="card" style="left:76px;top:1180px">
  <div class="card-photo" role="img" aria-label="Photo of a rendered two-storey townhouse"></div><span class="sold" style="left:27px;top:28px">SOLD</span>
  <h3 class="card-title">3/18 Coral Road<br>Ashbury,&nbsp; 6191</h3>
  <p class="card-text">Lanventore veritatis et quasi architecto beatae vitae dicta sunt enim ipsam voluptatem ..</p>
</article>
<article class="card" style="left:612px;top:1180px">
  <div class="card-photo" role="img" aria-label="Photo of a brick house with a paved driveway at night"></div><span class="sold" style="left:27px;top:28px">SOLD</span>
  <h3 class="card-title">41 Barley&nbsp; Street<br>Ashbury, 6191</h3>
  <p class="card-text">Lanventore veritatis et quasi architecto beatae vitae dicta sunt enim ipsam voluptatem ..</p>
</article>
<article class="card" style="left:76px;top:1408px">
  <div class="card-photo" role="img" aria-label="Photo of a white rendered house with a garage"></div><span class="sold" style="left:27px;top:28px">SOLD</span>
  <h3 class="card-title">9 Halloran Street<br>Ashbury, 6191</h3>
  <p class="card-text">Lanventore veritatis et quasi architecto beatae vitae dicta sunt enim ipsam voluptatem ..</p>
</article>
<article class="card" style="left:612px;top:1408px">
  <div class="card-photo" role="img" aria-label="Photo of a red brick townhouse with a double garage"></div><span class="sold" style="left:27px;top:28px">SOLD</span>
  <h3 class="card-title">5/30 Ellery Street<br>Marrowdale 6190</h3>
  <p class="card-text">Lanventore veritatis et quasi architecto beatae vitae dicta sunt enim ipsam voluptatem ..</p>
</article>

<section class="appraisal">
  <div class="appraisal-photo" role="img" aria-label="Photo of a backyard patio and pool at night"></div>
  <h2 class="section-title">Book An Appraisal</h2>
  <div class="field" style="top:152px">Name</div>
  <div class="field" style="top:200px">Email Address</div>
  <div class="field" style="top:248px">Phone No</div>
  <div class="field" style="top:298px">Address</div>
  <div class="field" style="top:346px">Preffered Time/Date</div>
  <div class="field area">Message</div>
  <a class="btn appraisal-submit" style="top:350px">Submit</a>
</section>

<h2 class="section-title" style="top:2136px">What Our Clients Think</h2>

<div class="quote" style="left:76px">
  <span class="quote-mark">&ldquo;</span>
  <p class="quote-body">We bought our first home through Dean and the process was easy and very straight forward. We felt confident buying our first home and extremely supported. We put a few offers forward on other properties with other local agents but we didn't feel that piece of mind that we felt with Dean..</p>
  <div class="quote-name">Marina &amp; Tomas</div>
  <div class="quote-place">Ashbury, 6191</div>
</div>
<div class="quote" style="left:436px">
  <span class="quote-mark">&ldquo;</span>
  <p class="quote-body">We bought our first home through Dean and the process was easy and very straight forward. We felt confident buying our first home and extremely supported. We put a few offers forward on other properties with other local agents but we didn't feel that piece of mind that we felt with Dean..</p>
  <div class="quote-name">Marina &amp; Tomas</div>
  <div class="quote-place">Ashbury, 6191</div>
</div>
<div class="quote" style="left:796px">
  <span class="quote-mark">&ldquo;</span>
  <p class="quote-body">We bought our first home through Dean and the process was easy and very straight forward. We felt confident buying our first home and extremely supported. We put a few offers forward on other properties with other local agents but we didn't feel that piece of mind that we felt with Dean..</p>
  <div class="quote-name">Marina &amp; Tomas</div>
  <div class="quote-place">Ashbury, 6191</div>
</div>

<footer class="contact">
  <h2 class="section-title">Contact Us</h2>
  <div class="addr-head">ADDRESS</div>
  <p class="addr"><span class="org">DEAN HARTWELL REAL ESTATE</span><br>Suite 14, 22 Larkspur Lane, Marrowdale,<br>WA 6190 Australia<br><br>0412 555 308<br>dean@gordonvale.com</p>
  <div class="map" role="img" aria-label="Street map showing the office location"></div>
  <div class="form-head">Alternatively you can fill in the following&nbsp; contact form:</div>
  <div class="cfield" style="left:614px;width:168px">Name</div>
  <div class="cfield" style="left:788px;width:166px">Email Address</div>
  <div class="cfield" style="left:960px;width:168px">Subject</div>
  <div class="cfield area">Message</div>
  <a class="btn contact-submit">Submit</a>
</footer>

<div class="copyright">Copyright &copy; 2018 Company Name&nbsp; All Right Reserved</div>

</body>
</html>
```